New LLC consulting company needs a business card design

I need a business card design for new company in Alexandria Virginia called TK Verdane Consulting LLC. The company is focused on consulting for defense and national security issues with expertise in nuclear and space topics. I would like to see designs that are simple and I am open to colors except for brown.

Target Market(s)

All businesses that are seeking consulting help

Industry/Entity Type

Consulting

Contact Information for Business Card

Name of company - TK Verdane Consulting LLC; name (Delia Pratt) President; email: prattdq47@mailvessa.com; Phone: 703-555-0142

Requirements
Must have
• The details described above
Nice to have
• I'm open to all ideas
Should not have
• No brown

```html
<!DOCTYPE html>
<html lang="en">
<head>
<meta charset="utf-8">
<title>TK Verdane Consulting LLC — Business Card</title>
<link rel="stylesheet" href="https://fonts.googleapis.com/css2?family=Josefin+Sans:wght@400;600&family=Lato:wght@400;900&display=swap">
<style>
  :root {
    --stage: #2b2b2b;
    --navy: #1a3147;
    --ink: #162c42;
    --sky: #6bbadc;
    --paper: #ffffff;
    --body: #222a33;
  }
  * { box-sizing: border-box; margin: 0; padding: 0; }
  html, body { width: 1200px; height: 875px; overflow: hidden; }
  body {
    background: var(--stage);
    font-family: "Lato", sans-serif;
    position: relative;
  }
  .card {
    position: absolute;
    width: 540px;
    height: 309px;
    border-radius: 18px;
    overflow: hidden;
  }
  .card--back { left: 50px; top: 140px; background: var(--navy); }
  .card--front { left: 610px; top: 426px; background: var(--paper); }

  .lockup {
    position: absolute;
    display: flex;
    align-items: center;
    gap: 18px;
  }
  .lockup__mark {
    border-radius: 50%;
    border: 3px solid currentColor;
    flex: none;
  }
  .lockup__text {
    font-family: "Josefin Sans", sans-serif;
    font-weight: 600;
    text-align: center;
    line-height: 1;
  }
  .lockup__name { display: block; letter-spacing: 0.02em; }
  .lockup__sub {
    display: flex;
    align-items: center;
    gap: 8px;
    margin-top: 6px;
    letter-spacing: 0.28em;
  }
  .lockup__sub::before, .lockup__sub::after {
    content: "";
    flex: 1;
    height: 1.5px;
    background: currentColor;
  }

  .card--back .lockup { left: 62px; top: 104px; color: var(--paper); }
  .card--back .lockup__mark { width: 92px; height: 92px; }
  .card--back .lockup__name { font-size: 44px; }
  .card--back .lockup__sub { font-size: 12px; }

  .card--front .lockup { left: 34px; top: 64px; color: var(--ink); }
  .card--front .lockup__name { font-size: 38px; }
  .card--front .lockup__sub { font-size: 11px; }

  .emblem {
    position: absolute;
    right: 40px;
    top: 26px;
    width: 170px;
    height: 170px;
    border-radius: 50%;
    border: 4px solid var(--ink);
  }

  .contact { position: absolute; left: 34px; top: 184px; }
  .contact__name {
    font-weight: 900;
    font-size: 24px;
    color: var(--ink);
    letter-spacing: 0.02em;
    line-height: 1.1;
  }
  .contact__role { font-size: 14px; color: var(--sky); margin-bottom: 10px; }
  .contact__line {
    display: flex;
    align-items: center;
    gap: 8px;
    font-size: 13px;
    color: var(--body);
    line-height: 1.6;
  }
  .contact__line svg { width: 13px; height: 13px; fill: var(--sky); flex: none; }
</style>
</head>
<body>

  <section class="card card--back" aria-label="Card back">
    <div class="lockup">
      <span class="lockup__mark" aria-hidden="true"></span>
      <div class="lockup__text">
        <span class="lockup__name">TK VERDANE</span>
        <span class="lockup__sub">CONSULTING LLC</span>
      </div>
    </div>
  </section>

  <section class="card card--front" aria-label="Card front">
    <div class="lockup">
      <div class="lockup__text">
        <span class="lockup__name">TK VERDANE</span>
        <span class="lockup__sub">CONSULTING LLC</span>
      </div>
    </div>
    <span class="emblem" aria-hidden="true"></span>

    <div class="contact">
      <p class="contact__name">DELIA PRATT</p>
      <p class="contact__role">President</p>
      <p class="contact__line">
        <svg viewBox="0 0 24 24" aria-hidden="true"><path d="M6.6 10.8a15.1 15.1 0 0 0 6.6 6.6l2.2-2.2a1 1 0 0 1 1-.25 11.4 11.4 0 0 0 3.6.57 1 1 0 0 1 1 1V20a1 1 0 0 1-1 1A17 17 0 0 1 3 4a1 1 0 0 1 1-1h3.5a1 1 0 0 1 1 1c0 1.25.2 2.45.57 3.57a1 1 0 0 1-.25 1z"/></svg>
        703-555-0142
      </p>
      <p class="contact__line">
        <svg viewBox="0 0 24 24" aria-hidden="true"><path d="M2 5h20v14H2zm2 2v.4l8 5.2 8-5.2V7zm0 2.8V17h16V9.8l-8 5.2z"/></svg>
        prattdq47@mailvessa.com
      </p>
    </div>
  </section>

</body>
</html>
```